Business Card Design

educational services
broker of essential services
So I love my The Velvet Kettle cards. I love the background.
I like the background on the copper valley card
I like a little part of each Meridel card
I want my card to stand out and be professional
I would also like somewhat of a brand
I do not want it to be specific to anything but the world and galaxy
I would like to be able to be used for everything, all encompassing
In spanish Cielo abierto, not sureother languages but i will do programs for other countries like China, Japan and Korea
Reason: It has been the first week of school and I have not been able to get the feedback I need.
Please change colors to Blue and GOld
Please add ~ over the n in Lorna
Please submit some vertical designs
Please include the world
Please make eagle a watermark
Make sure the Open Horizon doesnt have "preparatory school" under it
I am open to new designs and I will pay more after I chose a designer who seems to get all this stuff in my head!
Reason: Last minute designs were wonderful
Reason: I was out of town and not able to review the wonderful designs posted. I am narrowing the designs down now! I appreciate all the work done thus far.
Hello,
Thank you for all the designs. This is difficult. I have not been able to access them as I was able to last week so please be patient. If you also do web design please send me a message.
Again, thank you. I am down to just a few designs.
Sincerely,
Lorna Vickers Dunmore
I have been extremely busy, I should pick a design by the ned of this week. Thank you for your patience
Industry/Entity Type
Business
Contact Information for Business Card
Dr. Lorna Vickers Dunmore
www.ohacad.example
(555) 284-9306 US
lornajeanvickers@mailbox.example

```html
<!DOCTYPE html>
<html lang="en">
<head>
<meta charset="utf-8">
<title>Open Horizon Business Card</title>
<link href="https://fonts.googleapis.com/css2?family=Arvo:wght@400;700&display=swap" rel="stylesheet">
<style>
  :root {
    --backdrop: #ececec;
    --paper: #fbfbfa;
    --wine: #5c0e2e;
    --gold: #c8b41e;
    --ink-light: #ffffff;
  }
  * { margin: 0; padding: 0; box-sizing: border-box; }
  html, body {
    width: 1200px;
    height: 977px;
    overflow: hidden;
    background: var(--backdrop);
  }
  .stage {
    position: relative;
    width: 1200px;
    height: 977px;
    display: flex;
    align-items: center;
    justify-content: center;
  }
  .business-card {
    position: relative;
    width: 900px;
    height: 514px;
    background: var(--paper);
    overflow: hidden;
    box-shadow: 0 10px 30px rgba(0,0,0,0.15);
    font-family: "Arvo", "Rockwell", serif;
  }
  .card-shapes {
    position: absolute;
    inset: 0;
  }
  .brand {
    position: absolute;
    left: 100px;
    top: 112px;
    display: flex;
    align-items: center;
    gap: 12px;
    white-space: nowrap;
  }
  .brand-dot {
    width: 50px;
    height: 50px;
    border-radius: 50%;
    background: var(--wine);
  }
  .brand-name {
    font-family: "Arvo", serif;
    font-weight: 700;
    font-size: 38px;
    line-height: 1;
    color: var(--gold);
  }
  .holder-name {
    position: absolute;
    left: 496px;
    top: 168px;
    font-weight: 700;
    font-size: 24px;
    line-height: 1.2;
    color: var(--gold);
    white-space: nowrap;
  }
  .contact-list {
    position: absolute;
    left: 512px;
    top: 214px;
    list-style: none;
  }
  .contact-item {
    display: flex;
    align-items: center;
    gap: 10px;
    height: 34px;
    font-size: 17px;
    color: var(--ink-light);
    white-space: nowrap;
  }
  .contact-icon {
    width: 20px;
    height: 20px;
    flex: none;
  }
</style>
</head>
<body>
<main class="stage">
  <article class="business-card">
    <svg class="card-shapes" width="900" height="514" viewBox="0 0 900 514" aria-hidden="true">
      <rect x="0" y="0" width="900" height="24" fill="var(--wine)"/>
      <path d="M0 255 H480 V150 H900 V514 H0 Z" fill="var(--wine)"/>
      <rect x="100" y="180" width="390" height="18" rx="9" fill="var(--wine)"/>
    </svg>

    <div class="brand">
      <span class="brand-dot"></span>
      <span class="brand-name">Open Horizon</span>
    </div>

    <h1 class="holder-name">Dr. Lorna Vickers Dunmore</h1>

    <ul class="contact-list">
      <li class="contact-item">
        <svg class="contact-icon" viewBox="0 0 22 22" aria-hidden="true">
          <circle cx="11" cy="11" r="11" fill="var(--ink-light)"/>
          <path d="M7.5 5.5 l2 2.5 -1.2 1.5 c0.8 1.8 2.2 3.2 4 4 l1.5 -1.2 2.5 2 -1.3 2 c-4.5 -0.5 -8.5 -4.5 -9 -9 z" fill="var(--wine)"/>
        </svg>
        <span>(555) 284-9306 US</span>
      </li>
      <li class="contact-item">
        <svg class="contact-icon" viewBox="0 0 22 22" aria-hidden="true">
          <circle cx="11" cy="11" r="11" fill="var(--ink-light)"/>
          <rect x="5" y="7" width="12" height="8" fill="none" stroke="var(--wine)" stroke-width="1.5"/>
          <path d="M5 7 l6 5 6 -5" fill="none" stroke="var(--wine)" stroke-width="1.5"/>
        </svg>
        <span>lornajeanvickers@mailbox.example</span>
      </li>
      <li class="contact-item">
        <svg class="contact-icon" viewBox="0 0 22 22" aria-hidden="true">
          <circle cx="11" cy="11" r="11" fill="var(--ink-light)"/>
          <circle cx="11" cy="11" r="6" fill="none" stroke="var(--wine)" stroke-width="1.5"/>
          <path d="M5 11 H17 M11 5 c-3 3 -3 9 0 12 M11 5 c3 3 3 9 0 12" fill="none" stroke="var(--wine)" stroke-width="1.2"/>
        </svg>
        <span>www.ohacad.example</span>
      </li>
    </ul>
  </article>
</main>
</body>
</html>
```